Heritage Hollow Business Cards

Require a business card design. <br/><br/>Needs to include logo (either round or long version) plus these details:<br/>Maya Torvell<br/>Heritage Hollow<br/>maya@kelvadtrading.com.au<br/>02 6481 7395<br/>PO Box Glenwarra NSW 2791<br/>www.heritagehollow.com.au<br/><br/>I need in an editable format so that I can create for multiple staff members. <br/><br/>

Target Market(s)

We are an online store selling renovation products to home owners are builders. Looking for a classic classy design.

Industry/Entity Type

Home And Garden

Contact Information for Business Card

Maya Torvell
Heritage Hollow
maya@kelvadtrading.com.au
02 6481 7395
PO Box Glenwarra NSW 2791
www.heritagehollow.com.au

Colors

Designer to choose colors to be used in the design.

Requirements
Must have
• Must include Logo.

```html
<!DOCTYPE html>
<html lang="en">
<head>
<meta charset="utf-8">
<title>Heritage Hollow Business Cards</title>
<link href="https://fonts.googleapis.com/css2?family=Bitter:wght@500;700&family=Work+Sans:wght@400&display=swap" rel="stylesheet">
<style>
  :root {
    --ink: #1c1a1b;
    --card-dark: #221f20;
    --card-light: #f6f7f9;
    --paper-text: #2a2a2a;
    --backdrop: #d9d9d9;
    --white: #ffffff;
  }
  * { margin: 0; padding: 0; box-sizing: border-box; }
  html, body { width: 1200px; height: 900px; overflow: hidden; }
  body {
    background: var(--backdrop);
    position: relative;
    font-family: "Work Sans", sans-serif;
  }
  .card {
    position: absolute;
    left: 250px;
    width: 700px;
    height: 400px;
    box-shadow: 0 6px 18px rgba(0,0,0,0.18);
  }
  .card--back { top: 30px; background: var(--card-dark); }
  .card--front { top: 470px; background: var(--card-light); color: var(--paper-text); }

  .brand-mark {
    position: absolute;
    display: flex;
    align-items: center;
    gap: 18px;
  }
  .card--back .brand-mark {
    left: 50%; top: 50%;
    transform: translate(-50%, -50%);
  }
  .brand-mark__circle {
    width: 70px; height: 70px;
    border: 1.5px solid var(--white);
    border-radius: 50%;
  }
  .brand-mark__name {
    font-family: "Bitter", serif;
    font-weight: 500;
    font-size: 52px;
    color: var(--white);
    white-space: nowrap;
  }

  .front-emblem {
    position: absolute;
    right: 40px; top: 40px;
    width: 300px; height: 300px;
    border: 1.5px solid var(--ink);
    border-radius: 50%;
    display: flex;
    align-items: center;
    justify-content: center;
    text-align: center;
  }
  .front-emblem__name {
    font-family: "Bitter", serif;
    font-weight: 500;
    font-size: 50px;
    line-height: 1.05;
    color: var(--ink);
  }

  .edge-tab {
    position: absolute;
    left: 0; top: 98px;
    width: 16px; height: 46px;
    background: var(--ink);
  }
  .holder {
    position: absolute;
    left: 48px; top: 100px;
  }
  .holder__name {
    font-family: "Bitter", serif;
    font-weight: 700;
    font-size: 30px;
    letter-spacing: 3px;
    color: var(--ink);
    text-transform: uppercase;
  }
  .holder__company {
    font-size: 15px;
    letter-spacing: 0.5px;
    margin-top: 2px;
  }

  .contact {
    position: absolute;
    left: 48px; bottom: 42px;
    font-size: 15px;
    line-height: 1.45;
    letter-spacing: 0.4px;
  }
  .contact__address { margin-bottom: 8px; }
  .contact__line {
    display: flex;
    align-items: center;
    gap: 8px;
  }
  .contact__icon { width: 12px; height: 12px; flex: none; }
</style>
</head>
<body>

  <section class="card card--back">
    <div class="brand-mark">
      <span class="brand-mark__circle"></span>
      <span class="brand-mark__name">Heritage Hollow</span>
    </div>
  </section>

  <section class="card card--front">
    <span class="edge-tab"></span>

    <div class="holder">
      <h1 class="holder__name">Maya Torvell</h1>
      <p class="holder__company">Heritage Hollow</p>
    </div>

    <div class="front-emblem">
      <span class="front-emblem__name">Heritage<br>Hollow</span>
    </div>

    <div class="contact">
      <p class="contact__address">PO Box<br>Glenwarra NSW 2791</p>
      <p class="contact__line">
        <svg class="contact__icon" viewBox="0 0 12 12" aria-hidden="true">
          <path d="M3 1 L5 3.5 L4 5 Q5 7 7 8 L8.5 7 L11 9 L10 11 Q5 11 1 3 Z" fill="#2a2a2a"/>
        </svg>
        02 6481 7395
      </p>
      <p class="contact__line">
        <svg class="contact__icon" viewBox="0 0 12 12" aria-hidden="true">
          <rect x="1" y="2.5" width="10" height="7" fill="none" stroke="#2a2a2a" stroke-width="1.2"/>
          <path d="M1 2.5 L6 6.5 L11 2.5" fill="none" stroke="#2a2a2a" stroke-width="1.2"/>
        </svg>
        maya@kelvadtrading.com.au
      </p>
      <p class="contact__line">
        <svg class="contact__icon" viewBox="0 0 12 12" aria-hidden="true">
          <circle cx="6" cy="6" r="5" fill="none" stroke="#2a2a2a" stroke-width="1.1"/>
          <ellipse cx="6" cy="6" rx="2.2" ry="5" fill="none" stroke="#2a2a2a" stroke-width="1"/>
          <line x1="1" y1="6" x2="11" y2="6" stroke="#2a2a2a" stroke-width="1"/>
        </svg>
        www.heritagehollow.com.au
      </p>
    </div>
  </section>

</body>
</html>
```